Valdane Companies Business Card Design

We need a new business card for our Private Equity Real Estate Development firm, “Valdane” and our EB-5 regional center “Thornmere Regional Center” on one card. We prefer a design that is simple, elegant, and represents the luxury products we design and build as well as the financial security and stability our successful history has produced. We are an industry leader in our field and 3rd generation family business that has evolved into an institutional quality investment platform. Considered design size is standard business card dimensions (3.5 x 2 inches with an additional 1/8 inch space for design elements or backgrounds that extend beyond the finished size of your piece.

Target Market(s)

• High net worth individuals
• Highly skilled technical workers and physicians in the US seeking investment-based immigration opportunities
• Sophisticated private equity investors
• Intermediary partners include domestic attorneys and investment brokers, as well as international agent networks
• US real estate developers

Industry/Entity Type

Finance

Contact Information for Business Card

(Providing placeholder info for personal information, please design for longer character spaces, longer names and addresses etc..)
• Logo for Valdane
• Logo for Thornmere Regional Center
• Full name: Marcus Valdane
• Job title: CEO
• Email address: mvaldane@valdanecompanies.com
• Cell phone number: +1.555.314.2287
• Office number +1.555.628.4410
• Office address: Larkfield Court 5, 4817 Vista Orilla, Ashcombe, WA.
• Website: www.valdanecompanies.com

Font styles to use
Serif
Sans Serif

Colors
ec1f27
ffffff
000000

Requirements
Must have
• • Logo for Valdane
• • Logo for Thornmere Regional Center
• - Use rounded corners
• (See .ai file included for logos)
Nice to have
• • Simple, elegant design
• • Aesthetically compatible with our website design (www.valdanecompanies.com)
• • Color palette including but not limited to white, black, and red (as per logos)
Should not have
• - Not too much red color
• - Do not stack both logos on top of each other

```html
<!DOCTYPE html>
<html lang="en">
<head>
<meta charset="utf-8">
<title>Valdane Companies – Business Card</title>
<link rel="stylesheet" href="https://fonts.googleapis.com/css2?family=Lato:wght@400;700&family=Roboto:wght@400;500&display=swap">
<style>
  :root {
    --red: #ec1f27;
    --white: #ffffff;
    --black: #000000;
    --stage: #2a2a2c;
    --card: #1c1c1d;
    --card-back: #141415;
    --muted: #d9d9d9;
  }
  * { margin: 0; padding: 0; box-sizing: border-box; }
  html, body {
    width: 1200px; height: 900px; overflow: hidden;
    background: var(--stage);
  }
  .canvas {
    position: relative; width: 1200px; height: 900px;
    display: flex; flex-direction: column; align-items: center; justify-content: center; gap: 40px;
  }
  .card {
    position: relative; width: 700px; height: 400px;
    border-radius: 16px; overflow: hidden;
    box-shadow: 0 14px 30px rgba(0,0,0,.45);
  }
  .card-back {
    background: var(--card-back);
    display: flex; align-items: center; justify-content: center;
  }
  .back-texture {
    position: absolute; inset: 0;
    background: radial-gradient(ellipse at 75% 55%, #3a3a3c 0%, #1a1a1b 55%, #0e0e0f 100%);
  }
  .back-name {
    position: relative;
    font-family: "Lato", sans-serif; font-weight: 700;
    font-size: 40px; letter-spacing: 6px; text-transform: uppercase;
    color: var(--red);
  }
  .card-front {
    background: linear-gradient(160deg, #232324 0%, var(--card) 60%, #161617 100%);
  }
  .brand {
    position: absolute; left: 40px; top: 0; width: 290px; height: 100%;
    display: flex; align-items: center; justify-content: center; text-align: center;
  }
  .brand-name {
    font-family: "Lato", sans-serif; font-weight: 700;
    font-size: 30px; line-height: 1.15; letter-spacing: 2px; text-transform: uppercase;
    color: var(--red);
  }
  .divider {
    position: absolute; left: 355px; top: 80px; width: 2px; height: 200px;
    background: var(--white);
  }
  .contact {
    position: absolute; left: 385px; top: 80px; right: 20px;
    font-family: "Lato", sans-serif; color: var(--white);
  }
  .person-name {
    font-family: "Roboto", sans-serif; font-weight: 500;
    font-size: 30px; letter-spacing: 1px; text-transform: uppercase;
    color: var(--red); line-height: 1;
  }
  .person-title {
    font-family: "Roboto", sans-serif; font-weight: 400; font-size: 16px; color: var(--muted);
    margin: 4px 0 18px;
  }
  .address { font-size: 17px; line-height: 1.3; margin-bottom: 8px; }
  .detail-list { list-style: none; }
  .detail {
    display: flex; align-items: center; gap: 10px;
    font-size: 17px; line-height: 1.5;
  }
  .detail svg { width: 12px; height: 12px; flex: none; }
</style>
</head>
<body>
<main class="canvas">

  <section class="card card-back" aria-label="Card back">
    <div class="back-texture" role="img" aria-label="Dark embossed brand pattern"></div>
    <span class="back-name">Valdane</span>
  </section>

  <section class="card card-front" aria-label="Card front">
    <div class="brand">
      <span class="brand-name">Thornmere<br>Regional Center</span>
    </div>

    <div class="divider"></div>

    <div class="contact">
      <h1 class="person-name">Marcus Valdane</h1>
      <p class="person-title">CEO</p>
      <p class="address">Larkfield Court 5, 4817 Vista Orilla<br>Ashcombe, WA.</p>
      <ul class="detail-list">
        <li class="detail">
          <svg viewBox="0 0 12 12" aria-hidden="true"><path d="M2.5 1h2l1 2.5-1.2.8a6 6 0 0 0 3.4 3.4l.8-1.2 2.5 1v2a1 1 0 0 1-1 1A9.5 9.5 0 0 1 1.5 2a1 1 0 0 1 1-1z" fill="var(--red)"/></svg>
          +1.555.314.2287
        </li>
        <li class="detail">
          <svg viewBox="0 0 12 12" aria-hidden="true"><rect x="3" y="1" width="6" height="3" fill="var(--red)"/><rect x="1" y="4.5" width="10" height="4.5" rx="1" fill="var(--red)"/><rect x="3" y="8" width="6" height="3" fill="var(--red)"/></svg>
          +1.555.628.4410
        </li>
        <li class="detail">
          <svg viewBox="0 0 12 12" aria-hidden="true"><rect x="1" y="2.5" width="10" height="7" fill="none" stroke="var(--red)" stroke-width="1.2"/><path d="M1 2.5 6 6.5 11 2.5" fill="none" stroke="var(--red)" stroke-width="1.2"/></svg>
          mvaldane@valdanecompanies.com
        </li>
        <li class="detail">
          <svg viewBox="0 0 12 12" aria-hidden="true"><circle cx="6" cy="6" r="5" fill="none" stroke="var(--red)" stroke-width="1.1"/><ellipse cx="6" cy="6" rx="2.2" ry="5" fill="none" stroke="var(--red)" stroke-width="1"/><path d="M1 6h10" stroke="var(--red)" stroke-width="1"/></svg>
          www.valdanecompanies.com
        </li>
      </ul>
    </div>
  </section>

</main>
</body>
</html>
```